Healthcare and Professional IT Services Company need a redesigned business card

We are a IT Services company that targets small medical practices and professional business such as Attorneys, Accounts, Architects etc. We want to communicate a professional yet friendly image using recent logo redesign here on ArtHarbor. Like to see the colors blue and orange in the design. Must use the Tall Pine Computing as displayed in the new logo - then also want to incorporate the fish logo as well.

Target Market(s)

Small medical and professional services

Industry/Entity Type

It Company

Contact Information for Business Card

The usual stuff, place for name address phone website. Also maybe our tagline which is "hooked on technology"

Requirements
Must have
• My new logo and the fish somewhere on the card

```html
<!DOCTYPE html>
<html lang="en">
<head>
<meta charset="utf-8">
<title>Tall Pine Computing – Business Card</title>
<link rel="stylesheet" href="https://fonts.googleapis.com/css2?family=Raleway:wght@300;400;600&display=swap">
<style>
  :root {
    --page-bg: #e9e6e2;
    --card-blue-deep: #0f4f9c;
    --card-blue: #1f6fc4;
    --card-blue-light: #4b95dc;
    --frost: #eef2f6;
    --frost-edge: #cfdbe8;
    --blush: #f1c2c4;
    --brand-blue: #2a7cc0;
    --accent-orange: #f2b57a;
    --text-light: #ffffff;
  }
  * { margin: 0; padding: 0; box-sizing: border-box; }
  html, body {
    width: 1200px;
    height: 969px;
    overflow: hidden;
    background: var(--page-bg);
    font-family: "Raleway", sans-serif;
  }
  .canvas {
    position: relative;
    width: 1200px;
    height: 969px;
    display: flex;
    align-items: center;
    justify-content: center;
  }
  .business-card {
    position: relative;
    width: 1000px;
    height: 566px;
    border-radius: 26px;
    overflow: hidden;
    background: linear-gradient(100deg, var(--card-blue-light) 0%, var(--card-blue) 45%, var(--card-blue-deep) 100%);
    box-shadow: 0 18px 40px rgba(20, 40, 70, 0.25);
  }
  .mascot-area {
    position: absolute;
    left: 0;
    top: 40px;
    width: 540px;
    height: 500px;
    border-radius: 0 160px 200px 0;
    background:
      radial-gradient(ellipse at 45% 95%, var(--blush) 0%, rgba(241,194,196,0) 45%),
      linear-gradient(180deg, var(--frost) 0%, var(--frost-edge) 100%);
    opacity: 0.95;
  }
  .brand {
    position: absolute;
    left: 90px;
    top: 345px;
    display: flex;
    align-items: center;
    gap: 16px;
  }
  .brand-dot {
    width: 34px;
    height: 34px;
    border-radius: 50%;
    background: var(--brand-blue);
  }
  .brand-name {
    font-weight: 600;
    font-size: 40px;
    color: var(--brand-blue);
    letter-spacing: 0.5px;
  }
  .contact {
    position: absolute;
    right: 60px;
    top: 95px;
    text-align: right;
    color: var(--text-light);
    font-weight: 300;
  }
  .person-name {
    font-size: 46px;
    font-weight: 300;
    color: var(--accent-orange);
    line-height: 1.1;
  }
  .person-role {
    font-size: 25px;
    color: var(--accent-orange);
    margin-top: 4px;
  }
  .address {
    margin-top: 42px;
    font-size: 23px;
    line-height: 1.42;
    padding-right: 36px;
  }
  .contact-lines {
    margin-top: 30px;
    list-style: none;
    font-size: 23px;
  }
  .contact-lines li {
    display: flex;
    justify-content: flex-end;
    align-items: center;
    gap: 14px;
    height: 38px;
  }
  .contact-lines svg {
    width: 22px;
    height: 22px;
    fill: var(--text-light);
    flex: none;
  }
</style>
</head>
<body>
<div class="canvas">
  <div class="business-card">
    <div class="mascot-area" role="img" aria-label="Soft frosted area where the fish mascot illustration belongs"></div>

    <div class="brand">
      <span class="brand-dot"></span>
      <span class="brand-name">Tall Pine Computing</span>
    </div>

    <div class="contact">
      <p class="person-name">Alan Reyes</p>
      <p class="person-role">CEO/Founder</p>
      <p class="address">412 Cedar Hollow Road<br>Juneau<br>Alaska 99801</p>
      <ul class="contact-lines">
        <li>555 204 7719
          <svg viewBox="0 0 24 24" aria-hidden="true"><path d="M6.6 10.8a15.1 15.1 0 0 0 6.6 6.6l2.2-2.2c.3-.3.7-.4 1-.2 1.1.4 2.3.6 3.6.6.6 0 1 .4 1 1V20c0 .6-.4 1-1 1A17 17 0 0 1 3 4c0-.6.4-1 1-1h3.5c.6 0 1 .4 1 1 0 1.3.2 2.5.6 3.6.1.3 0 .7-.2 1z"/></svg>
        </li>
        <li>alan@tallpine.example
          <svg viewBox="0 0 24 24" aria-hidden="true"><path d="M3 5h18v14H3z M5 7v.4l7 4.6 7-4.6V7z" fill-rule="evenodd"/></svg>
        </li>
        <li>www.tallpine.example
          <svg viewBox="0 0 24 24" aria-hidden="true"><circle cx="12" cy="12" r="10"/></svg>
        </li>
      </ul>
    </div>
  </div>
</div>
</body>
</html>
```